Tiskoro

We need a business card for our company is a holding for different business all are different we try to have some air of relax and fun in our projects we add pictures of the office to give you an idea od the mood of the business

Business

```html
<!DOCTYPE html>
<html lang="en">
<head>
<meta charset="utf-8">
<title>Tiskoro — Business Card</title>
<link rel="stylesheet" href="https://fonts.googleapis.com/css2?family=Montserrat:wght@400;500;600&display=swap">
<style>
  :root {
    --backdrop: #d9d2c5;
    --card-light: #fbfbfb;
    --card-shade: #e3e3e3;
    --brand-yellow: #f4ea2c;
    --brand-brown: #6a4a30;
    --ink: #4a4a4a;
    --ink-soft: #6b6b6b;
  }
  * { margin: 0; padding: 0; box-sizing: border-box; }
  html, body {
    width: 1200px; height: 677px; overflow: hidden;
    background: var(--backdrop);
    font-family: "Montserrat", sans-serif;
  }
  .stage {
    position: relative; width: 1200px; height: 677px;
    display: flex; align-items: center; justify-content: center;
  }
  .card {
    position: relative; width: 860px; height: 490px; overflow: hidden;
    background: linear-gradient(135deg, var(--card-shade) 0%, var(--card-light) 45%, var(--card-light) 70%, var(--card-shade) 100%);
    box-shadow: 0 18px 40px rgba(60, 45, 25, 0.35);
  }
  .card-arcs { position: absolute; inset: 0; }
  .brand {
    position: absolute; top: 46px; right: 70px;
    display: flex; align-items: center; gap: 14px;
  }
  .brand-mark { width: 34px; height: 34px; background: var(--brand-yellow); }
  .brand-name {
    font-weight: 600; font-size: 34px; color: var(--brand-brown);
    letter-spacing: 0.5px;
  }
  .holder {
    position: absolute; left: 300px; top: 218px;
  }
  .holder-name {
    font-weight: 500; font-size: 27px; letter-spacing: 3px;
    color: var(--ink); text-transform: uppercase;
  }
  .holder-role {
    margin-top: 6px; font-size: 17px; color: var(--ink-soft); letter-spacing: 0.5px;
  }
  .contact {
    position: absolute; right: 70px; top: 150px;
    list-style: none; text-align: right;
    font-size: 14px; color: var(--ink); line-height: 1.35;
  }
  .contact-item {
    display: flex; justify-content: flex-end; align-items: center; gap: 10px;
    margin-bottom: 16px;
  }
  .contact-item svg { width: 14px; height: 14px; flex: none; fill: var(--ink-soft); }
  .contact-address { letter-spacing: 1px; }
</style>
</head>
<body>
<main class="stage">
  <article class="card">
    <svg class="card-arcs" viewBox="0 0 860 490" width="860" height="490" aria-hidden="true">
      <circle cx="20" cy="430" r="118" fill="none" stroke="var(--brand-yellow)" stroke-width="34"/>
      <circle cx="370" cy="560" r="168" fill="none" stroke="var(--brand-brown)" stroke-width="42"/>
    </svg>

    <header class="brand">
      <span class="brand-mark"></span>
      <span class="brand-name">Tiskoro</span>
    </header>

    <section class="holder">
      <h1 class="holder-name">Marcus Delaney</h1>
      <p class="holder-role">Managing Director</p>
    </section>

    <ul class="contact">
      <li class="contact-item contact-address">041 12th floor/Plaza<br>Harbour Road KTN</li>
      <li class="contact-item">012 555 0142
        <svg viewBox="0 0 24 24"><path d="M6.6 10.8a15.1 15.1 0 0 0 6.6 6.6l2.2-2.2c.3-.3.7-.4 1-.2 1.1.4 2.3.6 3.6.6.6 0 1 .4 1 1V20c0 .6-.4 1-1 1A17 17 0 0 1 3 4c0-.6.4-1 1-1h3.5c.6 0 1 .4 1 1 0 1.3.2 2.5.6 3.6.1.3 0 .7-.2 1z"/></svg>
      </li>
      <li class="contact-item">012 555 0178
        <svg viewBox="0 0 24 24"><path d="M7 1h10a2 2 0 0 1 2 2v18a2 2 0 0 1-2 2H7a2 2 0 0 1-2-2V3a2 2 0 0 1 2-2zm0 3v14h10V4zm5 15.5a1.2 1.2 0 1 0 0 2.4 1.2 1.2 0 0 0 0-2.4z"/></svg>
      </li>
      <li class="contact-item">012 555 0193
        <svg viewBox="0 0 24 24"><path d="M6 2h9l3 3v5H6zm-2 9h16a2 2 0 0 1 2 2v7a2 2 0 0 1-2 2H4a2 2 0 0 1-2-2v-7a2 2 0 0 1 2-2zm2 4v2h4v-2z"/></svg>
      </li>
      <li class="contact-item">hello@tiskoro.com
        <svg viewBox="0 0 24 24"><path d="M2 5h20v14H2zm2 2v.5l8 5 8-5V7zm0 3v7h16v-7l-8 5z"/></svg>
      </li>
      <li class="contact-item">www.tiskorogroup.com
        <svg viewBox="0 0 24 24"><path d="M12 2a10 10 0 1 0 0 20 10 10 0 0 0 0-20zm6.9 6h-3a15 15 0 0 0-1.3-3.9A8 8 0 0 1 18.9 8zM12 4c.8 1.2 1.5 2.5 1.9 4h-3.8c.4-1.5 1.1-2.8 1.9-4zM4.3 14a8 8 0 0 1 0-4h3.4a16 16 0 0 0 0 4zm.8 2h3a15 15 0 0 0 1.3 3.9A8 8 0 0 1 5.1 16zm3-8h-3a8 8 0 0 1 4.3-3.9C8.8 5.3 8.4 6.6 8.1 8zM12 20c-.8-1.2-1.5-2.5-1.9-4h3.8c-.4 1.5-1.1 2.8-1.9 4zm2.3-6H9.7a14 14 0 0 1 0-4h4.6a14 14 0 0 1 0 4zm.3 5.9c.6-1.2 1-2.5 1.3-3.9h3a8 8 0 0 1-4.3 3.9zm1.7-5.9a16 16 0 0 0 0-4h3.4a8 8 0 0 1 0 4z"/></svg>
      </li>
    </ul>
  </article>
</main>
</body>
</html>
```